Condo Debts Collection Business needs a Web Design (Contest)

I need a site for a client, who works with condo debts collection, and ensure all revenues provided by condo fees will be always available to the building manager of condo on a specific date, regardless of defaults.I have the logo of the companies, and some requirements on layout (kind of slider, menu options, phone number on a noble position, etc).
Updates

Designs look the same

Target Market(s)

I have two targets for this design: - Condominium's building manager. This target is looking for a solution to overdue debts on it's condo. - Residents on condominiums. This target wants to live in a better place, where their neighbors pay their condominium fees on time.

Number of Pages Required

1 page

Requirements
Must have
• - Slider with title, some short text related, a nice image (I prefer happy and/or peaceful family, people doing business, happy friends, and so on).
• - I have a special attention to menu. I'm looking for one I can have a nice effect, more elegant, charming, kind of innovative.
• - Phone number on the top (or clearly visible).
• - Member log in area or icon on the top (or clearly visible).
• - News/articles area.
• - Modern fonts, with good quality, sans-serif on areas where reading is more intensive (prefer Google web-fonts).
• - Colors specified on attached files.
• - Header similar or inspired by the "FILE 3"
Nice to have
• - Clear background color, cause it's better to read larger texts (like articles). Dark backgrounds makes reading difficult.
• - A site with effects (like shadows, lines, gradients, lights) is usually pretty.
• - I pay attention on beautiful footers.
Should not have
• - Images with a lot of money (I don't sell richness, I sell tranquility, peace, harmony, safety).
• - Poor menu.
• - Lots of curves. My customer asked for straight lines.

```html
<!DOCTYPE html>
<html lang="en">
<head>
<meta charset="utf-8">
<title>Serenara – Condo Fee Guarantee</title>
<link href="https://fonts.googleapis.com/css2?family=Montserrat:wght@500;600;700&family=Open+Sans:wght@400;600;700&display=swap" rel="stylesheet">
<style>
:root{
  --navy:#0e3a78;
  --navy-deep:#062a5e;
  --navy-mid:#0d4490;
  --orange:#e8691b;
  --orange-dark:#d4560f;
  --text:#333;
  --muted:#666;
  --line:#c9c9c9;
  --pale:#e9eef5;
  --white:#fff;
}
*{box-sizing:border-box;margin:0;padding:0}
html,body{width:1200px;height:3636px;overflow:hidden}
body{position:relative;background:var(--white);font-family:"Open Sans",Arial,sans-serif;color:var(--text)}
.abs{position:absolute}
.btn{position:absolute;display:flex;align-items:center;justify-content:center;background:linear-gradient(var(--orange),var(--orange-dark));color:var(--white);font:700 16px "Open Sans",Arial,sans-serif;letter-spacing:.5px;border-radius:27px;text-transform:uppercase}

/* hero */
.hero{position:absolute;left:0;top:0;width:1200px;height:710px;background:linear-gradient(180deg,#2f6fb0 0%,#7fb0d8 38%,#a9c08a 62%,#6d8a3a 82%,#4f6a24 100%)}
.hero-shade{position:absolute;inset:0;background:linear-gradient(90deg,rgba(10,30,60,.35),rgba(10,30,60,0) 55%)}
.brand{left:109px;top:34px;font:700 40px "Montserrat",Arial,sans-serif;color:var(--white);display:flex;align-items:center;gap:14px}
.brand-square{width:40px;height:40px;background:var(--white)}
.phone{left:623px;top:30px;color:var(--white);font:600 20px "Open Sans",Arial,sans-serif;display:flex;align-items:center;gap:8px}
.login{left:900px;top:22px;width:186px;height:46px;font-size:15px}
.nav{left:565px;top:90px;display:flex;gap:0;font:600 15px "Montserrat",Arial,sans-serif;color:var(--white)}
.nav span{position:absolute;white-space:nowrap}
.nav .active{color:var(--orange)}
.hero-title{left:109px;top:204px;font:700 50px/61px "Montserrat",Arial,sans-serif;color:var(--white);text-transform:uppercase}
.hero-text{left:109px;top:412px;width:460px;font:400 18px/30px "Open Sans",Arial,sans-serif;color:var(--white)}
.hero-btn{left:109px;top:514px;width:190px;height:62px}
.arrow{top:332px}

/* welcome */
.h2{position:absolute;left:0;width:1200px;text-align:center;font:600 40px "Montserrat",Arial,sans-serif;color:var(--navy);text-transform:uppercase}
.intro{left:240px;top:906px;width:720px;text-align:center;font-size:14.5px;line-height:29px;color:var(--muted)}
.feature{position:absolute;width:300px;text-align:center}
.feature-icon{width:130px;height:130px;margin:0 auto;border:1.5px solid var(--line);border-radius:50%;display:flex;align-items:center;justify-content:center}
.feature h3{margin-top:40px;font:500 22px "Montserrat",Arial,sans-serif;color:#222}
.feature p{margin-top:16px;font-size:13.5px;line-height:27px;color:var(--muted)}

/* who we are */
.who-photo{left:0;top:1733px;width:599px;height:471px;background:linear-gradient(135deg,#e7d6b8 0%,#b8a283 40%,#6e6a62 70%,#3f3d3a 100%)}
.who-panel{left:599px;top:1733px;width:601px;height:471px;background:var(--pale)}
.who-title{left:669px;top:1793px;font:600 40px "Montserrat",Arial,sans-serif;color:var(--navy);text-transform:uppercase}
.who-text{left:669px;top:1862px;width:424px;font-size:14.5px;line-height:30px;color:var(--muted)}
.who-btn{left:669px;top:2077px;width:162px;height:54px}

/* news */
.news-photo{position:absolute}
.news-title{font:600 21px/30px "Open Sans",Arial,sans-serif;color:#222}
.news-title.small{font-size:17px;line-height:27px}
.meta{display:flex;align-items:center;gap:8px;font-size:13px;color:#444;margin-top:10px}
.news-text{font-size:13.5px;line-height:26px;color:var(--muted);margin-top:10px}
.read-more{font:700 13px "Open Sans",Arial,sans-serif;color:var(--orange);text-transform:uppercase;margin-top:14px}
.view-btn{left:519px;top:3001px;width:162px;height:58px}

/* footer */
.footer{left:0;top:3168px;width:1200px;height:468px;background:linear-gradient(180deg,var(--navy-mid),var(--navy-deep))}
.f-head{top:3260px;font:600 16px "Montserrat",Arial,sans-serif;color:var(--white);text-transform:uppercase;letter-spacing:.5px}
.f-item{color:var(--white);font-size:13.5px;line-height:22px;display:flex;gap:14px}
.f-link{color:var(--white);font-size:13.5px}
.email{left:727px;top:3360px;width:267px;height:44px;background:var(--white);font-size:13px;color:#888;display:flex;align-items:center;padding-left:22px}
.subscribe{left:994px;top:3360px;width:92px;height:44px;background:var(--orange);color:var(--white);font:700 13px "Open Sans",Arial,sans-serif;display:flex;align-items:center;justify-content:center;text-transform:uppercase}
.social{position:absolute;top:3432px;width:42px;height:42px;border:1.5px solid var(--white);border-radius:50%}
.divider{left:100px;top:3534px;width:1000px;height:1px;background:rgba(255,255,255,.3)}
.copy{left:0;top:3568px;width:1200px;text-align:center;color:var(--white);font-size:13px}
</style>
</head>
<body>

<!-- HERO -->
<section class="hero" role="img" aria-label="Photo of a happy family in a sunny green field, father carrying a child on his shoulders"></section>
<div class="hero-shade abs" style="width:1200px;height:710px"></div>

<div class="brand abs"><span class="brand-square"></span>SERENARA</div>

<div class="phone abs">
  <svg width="18" height="18" viewBox="0 0 24 24"><path fill="#e8691b" d="M6.6 10.8a15 15 0 0 0 6.6 6.6l2.2-2.2c.3-.3.7-.4 1-.2 1.1.4 2.3.6 3.6.6.6 0 1 .4 1 1V20c0 .6-.4 1-1 1A17 17 0 0 1 3 4c0-.6.4-1 1-1h3.5c.6 0 1 .4 1 1 0 1.3.2 2.5.6 3.6.1.3 0 .7-.2 1z"/></svg>
  4150-2210 / 4150-2290
</div>
<div class="btn login">
  <svg width="14" height="14" viewBox="0 0 24 24" style="margin-right:8px"><circle cx="12" cy="7" r="5" fill="#fff"/><path d="M2 23c0-6 4-9 10-9s10 3 10 9z" fill="#fff"/></svg>Member Log In
</div>

<nav class="nav abs">
  <span class="active" style="left:0">HOME</span>
  <span style="left:77px">ABOUT US</span>
  <span style="left:189px">SERVICES</span>
  <span style="left:298px">NEWS</span>
  <span style="left:375px">CONTACT US</span>
  <span style="left:514px;top:1px"><svg width="16" height="16" viewBox="0 0 24 24"><circle cx="10" cy="10" r="7" fill="none" stroke="#fff" stroke-width="3"/><path d="M15 15l7 7" stroke="#fff" stroke-width="3"/></svg></span>
</nav>

<h1 class="hero-title abs">Our guarantee<br>and your peace<br>of mind</h1>
<p class="hero-text abs">Nam libero tempore, cum soluta nobis est eliedi optio cumque nihil impedit quo minus.</p>
<div class="btn hero-btn">Get More Info</div>

<svg class="abs arrow" style="left:42px" width="24" height="36" viewBox="0 0 24 36"><path d="M18 4L6 18l12 14" fill="none" stroke="#fff" stroke-width="3"/></svg>
<svg class="abs arrow" style="left:1136px" width="24" height="36" viewBox="0 0 24 36"><path d="M6 4l12 14L6 32" fill="none" stroke="#fff" stroke-width="3"/></svg>

<!-- WELCOME -->
<h2 class="h2" style="top:826px">Welcome to Serenara</h2>
<p class="intro abs">Nam libero tempore, cum soluta nobis est eligendi optio cumque nihil impedit quo minus id quod maxime placeat facere possimus, omnis voluptas assumenda est, omnis dolor repellendus</p>

<div class="feature" style="left:102px;top:1001px">
  <div class="feature-icon"><svg width="50" height="40" viewBox="0 0 50 40"><path d="M4 2v34h44" fill="none" stroke="#e8691b" stroke-width="3"/><path d="M10 30l10-12 8 7 14-15" fill="none" stroke="#e8691b" stroke-width="4"/><path d="M36 9h8v8" fill="none" stroke="#e8691b" stroke-width="3"/></svg></div>
  <h3>Maximize your profit</h3>
  <p>At vero eos et accusamus et iusto odio dig nissimos ducimus qui blanditiis praesentium voluptatum deleniti atque corr</p>
</div>
<div class="feature" style="left:449px;top:1001px">
  <div class="feature-icon"><svg width="46" height="46" viewBox="0 0 46 46"><rect x="4" y="8" width="30" height="32" rx="3" fill="none" stroke="#e8691b" stroke-width="3"/><path d="M18 28l20-20 5 5-20 20h-5z" fill="#e8691b"/></svg></div>
  <h3>Invoice Checking</h3>
  <p>At vero eos et accusamus et iusto odio dig nissimos ducimus qui blanditiis praesentium voluptatum deleniti atque corr</p>
</div>
<div class="feature" style="left:795px;top:1001px">
  <div class="feature-icon"><svg width="40" height="44" viewBox="0 0 40 44"><circle cx="20" cy="12" r="10" fill="#e8691b"/><path d="M2 42c0-11 8-17 18-17s18 6 18 17z" fill="#e8691b"/></svg></div>
  <h3>Control your accounts</h3>
  <p>At vero eos et accusamus et iusto odio dig nissimos ducimus qui blanditiis praesentium voluptatum deleniti atque corr</p>
</div>

<div class="feature" style="left:102px;top:1336px">
  <div class="feature-icon"><svg width="46" height="46" viewBox="0 0 46 46"><rect x="3" y="7" width="40" height="36" fill="none" stroke="#e8691b" stroke-width="3"/><rect x="3" y="7" width="40" height="9" fill="#e8691b"/><path d="M12 2v9M34 2v9" stroke="#e8691b" stroke-width="3"/><g fill="#e8691b"><rect x="9" y="21" width="6" height="5"/><rect x="20" y="21" width="6" height="5"/><rect x="31" y="21" width="6" height="5"/><rect x="9" y="31" width="6" height="5"/><rect x="20" y="31" width="6" height="5"/><rect x="31" y="31" width="6" height="5"/></g></svg></div>
  <h3>Collect at the right time</h3>
  <p>At vero eos et accusamus et iusto odio dig nissimos ducimus qui blanditiis praesentium voluptatum deleniti atque corr</p>
</div>
<div class="feature" style="left:449px;top:1336px">
  <div class="feature-icon"><svg width="52" height="34" viewBox="0 0 52 34"><rect x="2" y="2" width="48" height="30" fill="none" stroke="#e8691b" stroke-width="3"/><rect x="8" y="7" width="36" height="20" fill="#e8691b"/><circle cx="26" cy="17" r="7" fill="#fff"/></svg></div>
  <h3>First Party Collections</h3>
  <p>At vero eos et accusamus et iusto odio dig nissimos ducimus qui blanditiis praesentium voluptatum deleniti atque corr</p>
</div>
<div class="feature" style="left:795px;top:1336px">
  <div class="feature-icon"><svg width="50" height="44" viewBox="0 0 50 44"><path d="M4 6h30v20H16l-8 7v-7H4z" fill="none" stroke="#e8691b" stroke-width="3"/><path d="M20 16h26v20h-4v6l-7-6H20z" fill="#e8691b"/></svg></div>
  <h3>Connect with customers</h3>
  <p>At vero eos et accusamus et iusto odio dig nissimos ducimus qui blanditiis praesentium voluptatum deleniti atque corr</p>
</div>

<!-- WHO WE ARE -->
<div class="who-photo abs" role="img" aria-label="Photo of hands reviewing a chart report on a clipboard at a sunlit desk"></div>
<div class="who-panel abs"></div>
<h2 class="who-title abs">Who we are</h2>
<p class="who-text abs">Nam libero tempore, cum soluta nobis est eligendi oumquwe nihil impedit quo minus id quod maxime placeat facere posim us, omnis voluptas assumenda est, omnis dolor repellen ribus autem quibusdam et aut officiis debitis aut rerum necessitatib us saepe eveniet ut et voluptates repudiandae sint et molestiae non recusand que earum rerum.</p>
<div class="btn who-btn">Read More</div>

<!-- NEWS -->
<h2 class="h2" style="top:2320px">News</h2>

<div class="news-photo" style="left:111px;top:2436px;width:449px;height:276px;background:linear-gradient(135deg,#9bbf5a,#e2c8a8 50%,#6b8f3a)" role="img" aria-label="Photo of a smiling family hugging outdoors"></div>
<article class="abs" style="left:111px;top:2747px;width:449px">
  <h3 class="news-title">At vero eos et accusamus et iusto odio dig nissimos ducimus qui bland</h3>
  <div class="meta"><svg width="12" height="12" viewBox="0 0 12 12"><rect x="1" y="2" width="10" height="9" fill="#0e3a78"/></svg>28/02/2019 &nbsp;|&nbsp; <svg width="12" height="12" viewBox="0 0 12 12"><circle cx="6" cy="3.5" r="3" fill="#0e3a78"/><path d="M0 12c0-4 3-5 6-5s6 1 6 5z" fill="#0e3a78"/></svg>Marla Quent</div>
  <p class="news-text">Nam libero tempore, cum soluta nobis est eligendi optio cumque nihil impedit quo minus id quod maxime placeat facere.</p>
  <div class="read-more">Read More</div>
</article>

<div class="news-photo" style="left:591px;top:2436px;width:233px;height:223px;background:linear-gradient(160deg,#1f2c44,#9aa6b8 55%,#dfe3ea)" role="img" aria-label="Photo of a hand with a pen over printed bar charts"></div>
<article class="abs" style="left:851px;top:2442px;width:250px">
  <h3 class="news-title small">At vero eos et accusamus et iusto odio dignissi</h3>
  <div class="meta"><svg width="12" height="12" viewBox="0 0 12 12"><rect x="1" y="2" width="10" height="9" fill="#0e3a78"/></svg>28/02/2019 &nbsp;|&nbsp; <svg width="12" height="12" viewBox="0 0 12 12"><circle cx="6" cy="3.5" r="3" fill="#0e3a78"/><path d="M0 12c0-4 3-5 6-5s6 1 6 5z" fill="#0e3a78"/></svg>Marla Quent</div>
  <p class="news-text">Nam libero tempore, cum soluta nobis est eligendi optio cumque nihil impedit quo minus id quod maxi.</p>
  <div class="read-more">Read More</div>
</article>

<div class="news-photo" style="left:591px;top:2703px;width:233px;height:223px;background:linear-gradient(160deg,#c9b8a8,#8c7d74 50%,#4a4a4f)" role="img" aria-label="Photo of a finger pressing keys on a calculator"></div>
<article class="abs" style="left:851px;top:2707px;width:250px">
  <h3 class="news-title small">At vero eos et accusamus et iusto odio dignissi</h3>
  <div class="meta"><svg width="12" height="12" viewBox="0 0 12 12"><rect x="1" y="2" width="10" height="9" fill="#0e3a78"/></svg>28/02/2019 &nbsp;|&nbsp; <svg width="12" height="12" viewBox="0 0 12 12"><circle cx="6" cy="3.5" r="3" fill="#0e3a78"/><path d="M0 12c0-4 3-5 6-5s6 1 6 5z" fill="#0e3a78"/></svg>Marla Quent</div>
  <p class="news-text">Nam libero tempore, cum soluta nobis est eligendi optio cumque nihil impedit quo minus id quod maxi.</p>
  <div class="read-more">Read More</div>
</article>

<div class="btn view-btn">View More</div>

<!-- FOOTER -->
<footer class="footer abs"></footer>

<h4 class="f-head abs" style="left:109px">Contact Us</h4>
<div class="abs" style="left:112px;top:3300px;width:260px;display:flex;flex-direction:column;gap:14px">
  <div class="f-item"><svg width="12" height="16" viewBox="0 0 12 16" style="flex:none;margin-top:3px"><path d="M6 0a6 6 0 0 1 6 6c0 4-6 10-6 10S0 10 0 6a6 6 0 0 1 6-6z" fill="#fff"/><circle cx="6" cy="6" r="2" fill="#0d4490"/></svg><span>At vero eos et accusamus et iusto odio digm soluta nobis.</span></div>
  <div class="f-item"><svg width="14" height="14" viewBox="0 0 24 24" style="flex:none;margin-top:4px"><path fill="#fff" d="M6.6 10.8a15 15 0 0 0 6.6 6.6l2.2-2.2c.3-.3.7-.4 1-.2 1.1.4 2.3.6 3.6.6.6 0 1 .4 1 1V20c0 .6-.4 1-1 1A17 17 0 0 1 3 4c0-.6.4-1 1-1h3.5c.6 0 1 .4 1 1 0 1.3.2 2.5.6 3.6.1.3 0 .7-.2 1z"/></svg><span>+1 555 010 0188</span></div>
  <div class="f-item"><svg width="14" height="14" viewBox="0 0 14 14" style="flex:none;margin-top:4px"><rect x="0" y="4" width="14" height="8" fill="#fff"/><rect x="3" y="0" width="8" height="5" fill="#fff"/></svg><span>+1 555 010 0222</span></div>
  <div class="f-item"><svg width="14" height="12" viewBox="0 0 14 12" style="flex:none;margin-top:5px"><rect width="14" height="12" fill="#fff"/><path d="M0 0l7 6 7-6" fill="none" stroke="#0d4490" stroke-width="1.5"/></svg><span>info@serenara.com</span></div>
</div>

<h4 class="f-head abs" style="left:436px">Customer Service</h4>
<div class="abs" style="left:436px;top:3302px;display:flex;flex-direction:column;gap:15px">
  <span class="f-link">Delivery Information</span>
  <span class="f-link">My Account</span>
  <span class="f-link">Order Tracking</span>
  <span class="f-link">Reminder Service</span>
  <span class="f-link">Shipping, Returns &amp; Fees</span>
</div>

<h4 class="f-head abs" style="left:727px">Newsletter Subscription</h4>
<p class="abs" style="left:727px;top:3302px;width:340px;color:#fff;font-size:13.5px;line-height:26px">Register your Email Address to get information about us</p>
<div class="email abs">Email Address</div>
<div class="subscribe abs">Subscribe</div>
<span class="social" style="left:730px"></span>
<span class="social" style="left:784px"></span>
<span class="social" style="left:837px"></span>
<span class="social" style="left:891px"></span>

<div class="divider abs"></div>
<p class="copy abs">Copyrights © 2019, Serenara. All Rights Reserved.</p>

</body>
</html>
```